Website for my photography business

I need a website for my photography business, Bram Kellet Photography. I need a website that has a landing page with a cover photo of each kind of photography I do. For example, Nature, Weddings, Portraits and Architecture. I want it so that when someone comes onto my website they have to choose which kind of photography page they want to visit. So if they click on the wedding photo it will open to a page with my wedding portfolio images and a contact me button. If they choose nature photography I want them to be redirected to an e-commerce section where they can purchase prints. Architecture and Portraits should open up to their respective portfolios with about me and contact info. I like this kind of format because I want people who come to my website for a specific type of photography to be able to be directed there easily without having to look at a mix of other kinds of photography. I will provide a few files to use as placeholders. I have already purchased the bramkelletphotography.example domain name. A Wix website would be great because I am most familiar with it but I am open to anything.

Industry/Entity Type

Photographer

Number of Pages Required

5+ page

Requirements
Must have
• Landing Page and e-commerce

```html
<!DOCTYPE html>
<html lang="en">
<head>
<meta charset="utf-8">
<title>Bram Kellet Photography – Home</title>
<link rel="stylesheet" href="https://fonts.googleapis.com/css2?family=Poppins:wght@400;500;600;700&family=Great+Vibes&family=Parisienne&display=swap">
<style>
:root{
  --backdrop:#e2e2e2;
  --page:#ffffff;
  --topbar:#f4f4f4;
  --purple:#3e3468;
  --accent:#1f4d6b;
  --ink:#111111;
  --muted:#6b6b6b;
  --white:#ffffff;
  --script:#3e3468;
}
*{box-sizing:border-box;margin:0;padding:0}
html,body{width:1181px;height:1200px;overflow:hidden;background:var(--backdrop)}
body{font-family:"Poppins",sans-serif;color:var(--ink)}
.stage{position:absolute;left:0;top:0;width:1904px;height:1935px;transform:scale(0.62028);transform-origin:0 0}
.page{position:absolute;top:126px;width:761px;height:1682px;background:var(--page);box-shadow:0 2px 8px rgba(0,0,0,.18);overflow:hidden}
.page--a{left:141px}
.page--b{left:1001px}

.topbar{height:21px;background:var(--topbar);border-bottom:1px solid #e6e6e6;font-size:8px;color:#555;text-align:center;line-height:21px}
.header{position:relative;height:64px}
.brand{position:absolute;left:71px;top:22px;display:flex;align-items:center;gap:7px;font-size:13px;font-weight:500;color:var(--purple)}
.brand__dot{width:9px;height:9px;border-radius:50%;background:var(--purple)}
.social{position:absolute;display:flex;gap:4px}
.header .social{left:425px;top:22px}
.social span{width:22px;height:22px;border-radius:50%;border:1.3px solid #222;display:block}
.call{position:absolute;left:552px;top:19px;width:138px;height:28px;border-radius:14px;background:var(--accent);color:var(--white);font-size:10.5px;font-weight:600;text-align:center;line-height:28px}
.nav{height:25px;background:var(--purple);display:flex;padding-left:77px;font-size:9px;color:var(--white)}
.nav a{color:inherit;text-decoration:none;padding:0 10.5px;line-height:25px}
.nav a.is-active{background:var(--accent);padding:0 14px}

.hero{position:relative;height:343px;background:linear-gradient(100deg,#3b3a1c 0%,#7a6a22 22%,#c08a2a 42%,#6f7d3a 58%,#2a4f8f 75%,#3867b8 100%)}
.hero__ground{position:absolute;left:0;right:0;bottom:0;height:150px;background:linear-gradient(90deg,rgba(90,120,30,.7),rgba(150,110,40,.5) 40%,rgba(40,70,150,.3) 70%,rgba(30,60,140,.2))}
.hero__panel{position:absolute;left:219px;top:95px;width:320px;height:154px;background:rgba(40,35,60,.45);text-align:center;color:var(--white)}
.hero__title{font-family:"Great Vibes",cursive;font-size:30px;margin-top:6px;font-weight:400}
.hero__text{font-size:10.5px;font-weight:600;line-height:17px;margin-top:6px}
.btn{display:inline-block;background:var(--accent);color:var(--white);font-weight:700;border-radius:15px;text-align:center}
.hero .btn{width:112px;height:29px;line-height:29px;font-size:9.5px;margin-top:14px}
.arrow{position:absolute;top:158px;width:26px;height:26px}
.arrow--prev{left:21px}
.arrow--next{right:17px}

.work{position:relative;height:994px}
.work__title{position:absolute;left:0;right:0;top:53px;text-align:center;font-family:"Parisienne",cursive;font-size:27px;color:var(--script);font-weight:400}
.grid{position:absolute;left:94px;top:110px;width:574px;display:grid;grid-template-columns:287px 287px;grid-auto-rows:200px}
.cell{display:flex;flex-direction:column;align-items:center;justify-content:center;text-align:center}
.cell__title{font-size:19px;font-weight:600;color:var(--ink)}
.cell__text{font-size:8.5px;color:var(--muted);margin-top:10px}
.cell .btn{width:97px;height:28px;line-height:28px;font-size:8px;margin-top:15px}
.photo{display:block;width:287px;height:200px}
.photo--ring{background:linear-gradient(135deg,#8a7a6a,#b6a592 45%,#6e5d50)}
.photo--fox{background:linear-gradient(160deg,#2c3a2c,#5c6a4e 45%,#dfe6ee 75%,#f5f7fa)}
.photo--portrait{background:linear-gradient(135deg,#1a1a1a,#8c8c8c 45%,#d0d0d0 70%,#555)}
.photo--building{background:linear-gradient(180deg,#dfe6ee 0%,#c9ccc8 30%,#a9674f 55%,#8d8a80 80%,#6b6b62)}

.footer{position:absolute;left:0;right:0;bottom:0;height:245px;background:var(--purple);color:var(--white)}
.fcol{position:absolute;top:53px}
.fcol h3{font-size:10.5px;font-weight:500;text-transform:uppercase;margin-bottom:12px}
.fcol li{list-style:none;font-size:8px;line-height:17px}
.fcol--contact{left:71px}
.fcol--contact li{display:flex;gap:8px;align-items:flex-start;line-height:18.5px}
.fcol--contact li.addr{line-height:9px;margin-top:5px}
.fcol--contact svg{flex:none;margin-top:5px}
.fcol--contact u{text-underline-offset:2px}
.fcol--links{left:236px}
.fcol--info{left:381px}
.fcol--news{left:520px}
.news__input{width:169px;height:23px;border-radius:12px;background:var(--white);color:#777;font-size:8px;line-height:23px;padding-left:11px}
.news__submit{width:98px;height:22px;border-radius:11px;background:var(--accent);font-size:9px;font-weight:600;text-align:center;line-height:22px;margin-top:10px}
.footer .social{position:relative;left:13px;top:16px;gap:5px}
.footer .social span{background:var(--white);border:none}
.footer__rule{position:absolute;left:71px;right:71px;top:207px;height:1px;background:rgba(255,255,255,.18)}
.footer__copy{position:absolute;left:0;right:0;top:219px;text-align:center;font-size:8px}
</style>
</head>
<body>
<div class="stage">

  <!-- Layout A: labels only -->
  <section class="page page--a">
    <div class="topbar">Lorem ipsum dolor sit amet, consectetur adipiscing elit,</div>
    <header class="header">
      <div class="brand"><span class="brand__dot"></span>Bram Kellet Photography</div>
      <div class="social"><span></span><span></span><span></span><span></span></div>
      <div class="call">Call Us: 123-456-789</div>
    </header>
    <nav class="nav">
      <a class="is-active">Home</a><a>About Me</a><a>Nature</a><a>Weddings</a><a>Potraits</a><a>Architecture</a><a>Shop</a><a>portfolio</a><a>News</a><a>Contact Us</a>
    </nav>
    <div class="hero" role="img" aria-label="Autumn trees beside a blue river">
      <div class="hero__ground"></div>
      <svg class="arrow arrow--prev" viewBox="0 0 26 26"><circle cx="13" cy="13" r="12" fill="none" stroke="#fff" stroke-width="1.5"/><path d="M15 8l-5 5 5 5" fill="none" stroke="#fff" stroke-width="1.6"/></svg>
      <svg class="arrow arrow--next" viewBox="0 0 26 26"><circle cx="13" cy="13" r="12" fill="none" stroke="#fff" stroke-width="1.5"/><path d="M11 8l5 5-5 5" fill="none" stroke="#fff" stroke-width="1.6"/></svg>
      <div class="hero__panel">
        <h1 class="hero__title">Bram Kellet Photography</h1>
        <p class="hero__text">Lorem ipsum dolor sit amet, consectetur adipiscing<br>elit, sed do eiusmod tempor incididunt</p>
        <span class="btn">GET STARTED</span>
      </div>
    </div>
    <main class="work">
      <h2 class="work__title">Our Work</h2>
      <div class="grid">
        <div class="cell"><h3 class="cell__title">Weddings</h3></div>
        <div class="photo photo--ring" role="img" aria-label="Wedding ring resting on a stone"></div>
        <div class="photo photo--fox" role="img" aria-label="Red fox sitting in snow"></div>
        <div class="cell"><h3 class="cell__title">Nature</h3></div>
        <div class="cell"><h3 class="cell__title">Portrait</h3></div>
        <div class="photo photo--portrait" role="img" aria-label="Black and white portrait study"></div>
        <div class="photo photo--building" role="img" aria-label="Brick and glass building exterior"></div>
        <div class="cell"><h3 class="cell__title">Architecture</h3></div>
      </div>
    </main>
    <footer class="footer">
      <div class="fcol fcol--contact"><h3>Contact Info</h3><ul>
        <li><svg width="9" height="8" viewBox="0 0 9 8"><path d="M1 2h7v5H1z M2 0h5v2H2z" fill="#fff"/></svg>(888) 888-8888</li>
        <li><svg width="9" height="8" viewBox="0 0 9 8"><path d="M1 3h7v4H1z M2 0h5v3H2z" fill="#fff"/></svg>(888) 888-888</li>
        <li><svg width="9" height="7" viewBox="0 0 9 7"><rect width="9" height="7" fill="#fff"/><path d="M0 0l4.5 4L9 0" fill="none" stroke="#3e3468"/></svg><u>info@bramkelletphotography.example</u></li>
        <li class="addr"><svg width="7" height="9" viewBox="0 0 7 9"><path d="M3.5 9S0 5 0 3.5a3.5 3.5 0 017 0C7 5 3.5 9 3.5 9z" fill="#fff"/><circle cx="3.5" cy="3.5" r="1.3" fill="#3e3468"/></svg>#2888 Lorem ipsum dolor<br>sit amet, consectetur</li>
      </ul></div>
      <div class="fcol fcol--links"><h3>Quick Links</h3><ul><li>Home</li><li>About</li><li>Professional Gamer</li><li>Reviews</li><li>Gallery</li></ul></div>
      <div class="fcol fcol--info"><h3>Information</h3><ul><li>Terms &amp; Conditions</li><li>Privacy Policy</li><li>Disclaimer</li><li>Site Map</li><li>Contact Us</li></ul></div>
      <div class="fcol fcol--news"><h3>Newsletter Subscription</h3>
        <div class="news__input">Enter your email</div>
        <div class="news__submit">SUBMIT</div>
        <div class="social"><span></span><span></span><span></span><span></span></div>
      </div>
      <div class="footer__rule"></div>
      <p class="footer__copy">© Copyright 2020 Bram Kellet Photography, All Rights Reserved</p>
    </footer>
  </section>

  <!-- Layout B: labels with text and contact buttons -->
  <section class="page page--b">
    <div class="topbar">Lorem ipsum dolor sit amet, consectetur adipiscing elit,</div>
    <header class="header">
      <div class="brand"><span class="brand__dot"></span>Bram Kellet Photography</div>
      <div class="social"><span></span><span></span><span></span><span></span></div>
      <div class="call">Call Us: 123-456-789</div>
    </header>
    <nav class="nav">
      <a class="is-active">Home</a><a>About Me</a><a>Nature</a><a>Weddings</a><a>Potraits</a><a>Architecture</a><a>Shop</a><a>portfolio</a><a>News</a><a>Contact Us</a>
    </nav>
    <div class="hero" role="img" aria-label="Autumn trees beside a blue river">
      <div class="hero__ground"></div>
      <svg class="arrow arrow--prev" viewBox="0 0 26 26"><circle cx="13" cy="13" r="12" fill="none" stroke="#fff" stroke-width="1.5"/><path d="M15 8l-5 5 5 5" fill="none" stroke="#fff" stroke-width="1.6"/></svg>
      <svg class="arrow arrow--next" viewBox="0 0 26 26"><circle cx="13" cy="13" r="12" fill="none" stroke="#fff" stroke-width="1.5"/><path d="M11 8l5 5-5 5" fill="none" stroke="#fff" stroke-width="1.6"/></svg>
      <div class="hero__panel">
        <h1 class="hero__title">Bram Kellet Photography</h1>
        <p class="hero__text">Lorem ipsum dolor sit amet, consectetur adipiscing<br>elit, sed do eiusmod tempor incididunt</p>
        <span class="btn">GET STARTED</span>
      </div>
    </div>
    <main class="work">
      <h2 class="work__title">Our Work</h2>
      <div class="grid">
        <div class="cell"><h3 class="cell__title">Weddings</h3><p class="cell__text">Lorem ipsum dolor sit amet, consectetur elit,</p><span class="btn">CONTACT ME</span></div>
        <div class="photo photo--ring" role="img" aria-label="Wedding ring resting on a stone"></div>
        <div class="photo photo--fox" role="img" aria-label="Red fox sitting in snow"></div>
        <div class="cell"><h3 class="cell__title">Nature</h3><p class="cell__text">Lorem ipsum dolor sit amet, consectetur elit,</p><span class="btn">CONTACT ME</span></div>
        <div class="cell"><h3 class="cell__title">Portrait</h3><p class="cell__text">Lorem ipsum dolor sit amet, consectetur elit,</p><span class="btn">CONTACT ME</span></div>
        <div class="photo photo--portrait" role="img" aria-label="Black and white portrait study"></div>
        <div class="photo photo--building" role="img" aria-label="Brick and glass building exterior"></div>
        <div class="cell"><h3 class="cell__title">Architecture</h3><p class="cell__text">Lorem ipsum dolor sit amet, consectetur elit,</p><span class="btn">CONTACT ME</span></div>
      </div>
    </main>
    <footer class="footer">
      <div class="fcol fcol--contact"><h3>Contact Info</h3><ul>
        <li><svg width="9" height="8" viewBox="0 0 9 8"><path d="M1 2h7v5H1z M2 0h5v2H2z" fill="#fff"/></svg>(888) 888-8888</li>
        <li><svg width="9" height="8" viewBox="0 0 9 8"><path d="M1 3h7v4H1z M2 0h5v3H2z" fill="#fff"/></svg>(888) 888-888</li>
        <li><svg width="9" height="7" viewBox="0 0 9 7"><rect width="9" height="7" fill="#fff"/><path d="M0 0l4.5 4L9 0" fill="none" stroke="#3e3468"/></svg><u>info@bramkelletphotography.example</u></li>
        <li class="addr"><svg width="7" height="9" viewBox="0 0 7 9"><path d="M3.5 9S0 5 0 3.5a3.5 3.5 0 017 0C7 5 3.5 9 3.5 9z" fill="#fff"/><circle cx="3.5" cy="3.5" r="1.3" fill="#3e3468"/></svg>#2888 Lorem ipsum dolor<br>sit amet, consectetur</li>
      </ul></div>
      <div class="fcol fcol--links"><h3>Quick Links</h3><ul><li>Home</li><li>About</li><li>Professional Gamer</li><li>Reviews</li><li>Gallery</li></ul></div>
      <div class="fcol fcol--info"><h3>Information</h3><ul><li>Terms &amp; Conditions</li><li>Privacy Policy</li><li>Disclaimer</li><li>Site Map</li><li>Contact Us</li></ul></div>
      <div class="fcol fcol--news"><h3>Newsletter Subscription</h3>
        <div class="news__input">Enter your email</div>
        <div class="news__submit">SUBMIT</div>
        <div class="social"><span></span><span></span><span></span><span></span></div>
      </div>
      <div class="footer__rule"></div>
      <p class="footer__copy">© Copyright 2020 Bram Kellet Photography, All Rights Reserved</p>
    </footer>
  </section>

</div>
</body>
</html>
```